Business card design for holistic health care clinic

We need a double-sided business card design for our holistic health care clinic that integrates our logo design and also its color scheme. My business is called Valmira. It is an integrative medicine clinic. You have already done the logo for me. Please ensure an elegant and upscale design that is not cluttered, but still has all the necessary information (please see below for details).

Target Market(s)

Wellness, fitness, rehabilitation for educated, well-traveled open-minded clients who are focused on natural, organic, balanced and preventive healthcare and lifestyle.

Industry/Entity Type

Medical

Contact Information for Business Card

Modern, clean.

Number of Pages Required

1 page

Font styles to use
Serif
Sans Serif

Colors

Designer to choose colors to be used in the design.

Requirements
Must have
• Logo on one side, all other information on the other side.
• Other information should include:
• Tobias Wrenfeld - DOE, CPT, LMT
• 4100 East Marrow Drive
• Austin, TX 78119
• 512 555 0148
• 818 555 0192
• info@ValmiraHealth.example
• t.wrenfeld@ValmiraHealth.example
Nice to have
• Darker background on front - but not totally black - shaded/dark gray.

```html
<!DOCTYPE html>
<html lang="en">
<head>
<meta charset="utf-8">
<title>Valmira – Business Card</title>
<link href="https://fonts.googleapis.com/css2?family=Montserrat:wght@400;500;700;800&display=swap" rel="stylesheet">
<style>
  :root{
    --blue:#1b8fd2;
    --charcoal:#2a2a2c;
    --band:#262628;
    --paper:#ffffff;
    --grey-text:#555a60;
    --stage:#e6e7ea;
  }
  *{box-sizing:border-box;margin:0;padding:0}
  html,body{width:1200px;height:852px;overflow:hidden}
  body{background:var(--stage);font-family:"Montserrat",sans-serif;position:relative}
  .card{position:absolute;left:280px;width:640px;height:366px;border-radius:18px;overflow:hidden;box-shadow:0 6px 18px rgba(0,0,0,.18)}
  .card--front{top:34px;background:var(--charcoal)}
  .card--back{top:440px;background:var(--paper)}

  .brand{position:absolute;text-align:center;color:var(--blue)}
  .brand__name{font-weight:800;letter-spacing:2px;line-height:1}
  .brand__tagline{font-weight:700;margin-top:6px;line-height:1}
  .card--front .brand{left:0;right:0;top:128px}
  .card--front .brand__name{font-size:78px}
  .card--front .brand__tagline{font-size:21px}
  .card--back .brand{left:150px;width:300px;top:58px}
  .card--back .brand__name{font-size:58px}
  .card--back .brand__tagline{font-size:16px}

  .rule{position:absolute;height:1px;background:var(--blue)}
  .rule--top{left:330px;right:28px;top:160px}
  .rule--contact{left:28px;width:300px;top:246px}

  .holder{position:absolute;right:34px;top:178px;text-align:right}
  .holder__name{font-weight:800;font-size:23px;color:var(--blue);letter-spacing:.3px}
  .holder__creds{font-weight:500;font-size:12px;color:var(--grey-text);margin-top:3px}

  .contact{position:absolute;left:30px;top:254px;list-style:none}
  .contact li{display:flex;align-items:center;gap:9px;font-size:12.5px;color:var(--grey-text);height:15px}
  .contact svg{width:11px;height:11px;flex:none;fill:none;stroke:var(--blue);stroke-width:1.6}

  .band{position:absolute;left:0;right:0;top:320px;height:32px;background:var(--band);display:flex;align-items:center;justify-content:flex-end;padding-right:34px}
  .band__address{color:#fff;font-size:12.5px;font-weight:500;letter-spacing:.2px}
  .stripe{position:absolute;left:0;right:0;top:352px;height:14px;background:var(--blue)}
</style>
</head>
<body>

<section class="card card--front" aria-label="Card front">
  <div class="brand">
    <div class="brand__name">VALMIRA</div>
    <div class="brand__tagline">Integrative Holistic Medicine</div>
  </div>
</section>

<section class="card card--back" aria-label="Card back">
  <div class="brand">
    <div class="brand__name">VALMIRA</div>
    <div class="brand__tagline">Integrative Holistic Medicine</div>
  </div>

  <div class="rule rule--top"></div>

  <div class="holder">
    <div class="holder__name">TOBIAS WRENFELD</div>
    <div class="holder__creds">DOE, CPT, LMT</div>
  </div>

  <div class="rule rule--contact"></div>

  <ul class="contact">
    <li>
      <svg viewBox="0 0 12 12"><path d="M2.5 1.5l2 2-1 1.2c.6 1.4 1.6 2.4 3 3l1.2-1 2 2-1.4 1.6C5 10 2 7 .9 2.9z"/></svg>
      512 555 0148
    </li>
    <li>
      <svg viewBox="0 0 12 12"><rect x="3" y="1" width="6" height="10" rx="1"/><path d="M5.5 9h1"/></svg>
      818 555 0192
    </li>
    <li>
      <svg viewBox="0 0 12 12"><rect x="1" y="2.5" width="10" height="7" rx=".8"/><path d="M1.3 3l4.7 3.6L10.7 3"/></svg>
      info@ValmiraHealth.example
    </li>
    <li>
      <svg viewBox="0 0 12 12"><circle cx="6" cy="6" r="4.8"/><path d="M1.2 6h9.6M6 1.2c-2.4 2.6-2.4 7 0 9.6M6 1.2c2.4 2.6 2.4 7 0 9.6"/></svg>
      t.wrenfeld@ValmiraHealth.example
    </li>
  </ul>

  <div class="band"><span class="band__address">4100 East Marrow Drive Austin, TX 78119</span></div>
  <div class="stripe"></div>
</section>

</body>
</html>
```